Tolbek cards

I want a simple business card that pops.
Logo on one side.
On side two i want.
"Are you thinking about a new building on your property, or renovating an existing structure? Contact".....
Owners Name: Dale Whitacre
Owners Phone number: 610-555-0187
Address:4076 Copper Ridge RD, Millbrook, PA 16930
Committed to Quality, Service, and Integrity

```html
<!DOCTYPE html>
<html lang="en">
<head>
<meta charset="utf-8">
<title>Tolbek Builders – Business Cards</title>
<link rel="stylesheet" href="https://fonts.googleapis.com/css2?family=Roboto:wght@400;500;700&family=Roboto+Condensed:wght@700&display=swap">
<style>
  :root {
    --backdrop: #262626;
    --card: #efefef;
    --brown: #4a3426;
    --tan: #9c8166;
    --tan-dark: #6e5440;
    --white: #ffffff;
    --ink: #2b1f17;
    --rule: #b9a58f;
  }
  * { box-sizing: border-box; margin: 0; padding: 0; }
  html, body { width: 1200px; height: 576px; overflow: hidden; background: var(--backdrop); }
  .canvas { position: relative; width: 1200px; height: 576px; font-family: "Roboto", Arial, sans-serif; }

  .card { position: absolute; top: 139px; width: 484px; height: 291px; background: var(--card); border-radius: 10px; overflow: hidden; }
  .card--front { left: 102px; }
  .card--back { left: 596px; }

  /* Front */
  .front-mark { position: absolute; left: 205px; top: 50px; width: 74px; height: 74px; background: var(--brown); }
  .front-brand { position: absolute; left: 0; right: 0; top: 140px; text-align: center; color: var(--brown); font-weight: 700; }
  .front-brand__name { display: block; font-size: 54px; letter-spacing: 3px; line-height: 1; text-transform: uppercase; }
  .front-brand__sub { display: block; font-size: 16px; letter-spacing: 3px; margin-top: 6px; text-transform: uppercase; }
  .front-band { position: absolute; left: 0; right: 0; bottom: 0; height: 30px; background: linear-gradient(90deg, var(--tan), var(--tan-dark)); color: var(--white); font-size: 12.5px; text-align: center; line-height: 30px; }

  /* Back */
  .back-decor { position: absolute; left: 0; top: 0; width: 162px; height: 100%; background: linear-gradient(135deg, var(--brown), #5b4232); }
  .back-mark { position: absolute; left: 214px; top: 30px; width: 50px; height: 50px; background: var(--brown); }
  .back-brand { position: absolute; right: 18px; top: 28px; text-align: right; color: var(--brown); font-weight: 700; }
  .back-brand__name { display: block; font-size: 37px; letter-spacing: 1px; line-height: 1; text-transform: uppercase; }
  .back-brand__sub { display: block; font-size: 12px; letter-spacing: 3px; margin-top: 4px; text-transform: uppercase; }
  .pitch { position: absolute; left: 116px; right: 0; top: 97px; height: 53px; background: var(--tan); clip-path: polygon(0 0, 100% 0, 100% 100%, 8% 100%); color: var(--white); font-family: "Roboto Condensed", "Arial Narrow", sans-serif; font-weight: 700; font-size: 12px; line-height: 16px; text-align: right; padding: 8px 15px 0 0; text-transform: uppercase; }
  .pitch__contact { position: absolute; right: 14px; top: 143px; width: 82px; height: 16px; border-radius: 8px; background: var(--brown); color: var(--white); font-family: "Roboto Condensed", "Arial Narrow", sans-serif; font-weight: 700; font-size: 11.5px; text-align: center; line-height: 16px; text-transform: uppercase; }
  .contact { position: absolute; right: 15px; top: 167px; text-align: right; }
  .contact__name { font-size: 19px; font-weight: 700; color: var(--brown); letter-spacing: .5px; text-transform: uppercase; }
  .contact__name-last { color: var(--tan); }
  .contact__phone { font-size: 12.5px; font-weight: 700; color: var(--ink); margin-top: 5px; }
  .contact__address { font-size: 12px; color: var(--tan); margin-top: 4px; }
  .back-rule { position: absolute; left: 188px; right: 15px; top: 243px; height: 1px; background: var(--rule); }
  .back-tagline { position: absolute; right: 15px; top: 255px; font-size: 12.5px; color: var(--ink); }
</style>
</head>
<body>
<main class="canvas">
  <section class="card card--front">
    <div class="front-mark"></div>
    <div class="front-brand">
      <span class="front-brand__name">Tolbek</span>
      <span class="front-brand__sub">Builders LLC</span>
    </div>
    <div class="front-band">Committed to Quality, Service &amp; Integrity</div>
  </section>

  <section class="card card--back">
    <div class="back-decor" role="img" aria-label="Large angular brand decoration in dark brown"></div>
    <div class="back-mark"></div>
    <div class="back-brand">
      <span class="back-brand__name">Tolbek</span>
      <span class="back-brand__sub">Builders LLC</span>
    </div>
    <div class="pitch">Are you thinking about a new building on your<br>property, or renovating an existing structure?</div>
    <div class="pitch__contact">Contact</div>
    <div class="contact">
      <p class="contact__name">Dale <span class="contact__name-last">Whitacre</span></p>
      <p class="contact__phone">Call: 610-555-0187</p>
      <p class="contact__address">Add.: 4076 Copper Ridge RD, Millbrook, PA 16930</p>
    </div>
    <div class="back-rule"></div>
    <p class="back-tagline">Committed to Quality, Service &amp; Integrity</p>
  </section>
</main>
</body>
</html>
```